Velk Partners Building Business Cards

We need a business card that reflects our business as "Solar Experts" in San Diego. Browse our website www.velkpartners.example our License needs to be displayed as "CSLB# 3867140" our phone number is (619) 555-0187

Save thousands on your electric bills and increase the value of your home while helping to protect the environment. Our solar installation experts will help you design the system that's right for you, using only the highest quality equipment that will look great and give you ideal performance. Our goal is to make you energy independent, and get your electric bill to 0.

Paul Osterby
(619) 555-0187
paul@velkpartners.example

Target Market(s)

Home owners in san diego looking for solar

Industry/Entity Type

Solar Energy

Contact Information for Business Card

Paul Osterby
(619) 555-0187
paul@velkpartners.example

Font styles to use
Other font styles liked:
• Use our logo font

Requirements
Must have
• License needs to be displayed as "CSLB# 3867140" our phone number is (619) 555-0187
Nice to have
• Real images of rooftop home solar in san diego
Should not have
• our business address

```html
<!DOCTYPE html>
<html lang="en">
<head>
<meta charset="utf-8">
<title>Velk Partners Building – Business Cards</title>
<link rel="stylesheet" href="https://fonts.googleapis.com/css2?family=Open+Sans:wght@400;600;700&family=Oswald:wght@500&display=swap">
<style>
  :root {
    --navy: #1f4a85;
    --navy-text: #1b3f7a;
    --amber: #f5a81c;
    --ink: #2a2a2a;
    --paper: #ffffff;
    --backdrop: #e9e9e9;
  }
  * { box-sizing: border-box; margin: 0; padding: 0; }
  html, body { width: 1200px; height: 786px; overflow: hidden; }
  body {
    background: var(--backdrop);
    font-family: "Open Sans", Arial, sans-serif;
    position: relative;
  }
  .card {
    position: absolute;
    top: 250px;
    width: 486px;
    height: 276px;
    box-shadow: 0 2px 6px rgba(0,0,0,0.18);
  }
  .card--front { left: 122px; background: var(--paper); }
  .card--back { left: 617px; background: var(--navy); }

  .wordmark {
    display: flex;
    align-items: center;
    gap: 7px;
    font-weight: 700;
    white-space: nowrap;
  }
  .wordmark__dot { border-radius: 50%; background: var(--amber); flex: none; }

  .card--front .wordmark {
    position: absolute; left: 22px; top: 42px;
    font-size: 18px; color: var(--navy-text);
  }
  .card--front .wordmark__dot { width: 14px; height: 14px; }

  .license {
    position: absolute; left: 290px; top: 70px;
    font-size: 10.5px; font-weight: 700; color: var(--navy-text);
  }

  .person {
    position: absolute; left: 0; top: 186px;
    display: flex; align-items: center;
  }
  .person__bar { width: 9px; height: 23px; background: var(--amber); margin-right: 20px; }
  .person__name {
    font-family: "Oswald", "Arial Narrow", sans-serif;
    font-weight: 500; font-size: 22px; letter-spacing: 0.2px;
    color: var(--navy-text); line-height: 1;
  }
  .person__name .accent { color: var(--amber); }

  .contact {
    position: absolute; left: 290px; top: 183px;
    list-style: none; font-size: 12px; color: var(--ink);
  }
  .contact li { display: flex; align-items: center; height: 18px; }
  .contact svg { width: 11px; height: 11px; margin-right: 9px; flex: none; }
  .contact .accent { color: var(--amber); }

  .card--back .wordmark {
    position: absolute; left: 0; right: 0; top: 120px;
    justify-content: center;
    font-size: 32px; color: #ffffff; gap: 12px;
  }
  .card--back .wordmark__dot { width: 26px; height: 26px; }
  .card--back .website {
    position: absolute; left: 0; right: 0; top: 230px;
    text-align: center; font-size: 12.5px; font-weight: 600;
    color: #ffffff; letter-spacing: 0.3px;
  }
  .card--back .website .accent { color: var(--amber); }
</style>
</head>
<body>
  <section class="card card--front" aria-label="Business card front">
    <div class="wordmark"><span class="wordmark__dot"></span>Velk Partners Building</div>
    <p class="license">License-"CSLB# 3867140"</p>
    <div class="person">
      <span class="person__bar"></span>
      <p class="person__name">PAUL <span class="accent">OSTERBY</span></p>
    </div>
    <ul class="contact">
      <li>
        <svg viewBox="0 0 12 12" aria-hidden="true"><rect x="3" y="0.7" width="6" height="10.6" rx="1" fill="none" stroke="#2a2a2a" stroke-width="1.2"/><line x1="5" y1="9.3" x2="7" y2="9.3" stroke="#2a2a2a" stroke-width="1"/></svg>
        (619) 555-0187
      </li>
      <li>
        <svg viewBox="0 0 12 12" aria-hidden="true"><rect x="0.7" y="2.2" width="10.6" height="7.6" fill="none" stroke="#2a2a2a" stroke-width="1"/><polyline points="0.7,2.2 6,6.6 11.3,2.2" fill="none" stroke="#2a2a2a" stroke-width="1"/></svg>
        paul@velkpartners.example
      </li>
      <li>
        <svg viewBox="0 0 12 12" aria-hidden="true"><circle cx="6" cy="6" r="5.2" fill="none" stroke="#2a2a2a" stroke-width="1"/><ellipse cx="6" cy="6" rx="2.3" ry="5.2" fill="none" stroke="#2a2a2a" stroke-width="0.9"/><line x1="0.8" y1="6" x2="11.2" y2="6" stroke="#2a2a2a" stroke-width="0.9"/></svg>
        www.<span class="accent">velkpartners</span>.example
      </li>
    </ul>
  </section>

  <section class="card card--back" aria-label="Business card back">
    <div class="wordmark"><span class="wordmark__dot"></span>Velk Partners Building</div>
    <p class="website">www.<span class="accent">velkpartners</span>.example</p>
  </section>
</body>
</html>
```